The design should look similar to the uploaded example to accommodate the information needed for a business card template. I would like to see the colors orange and charcoal grey incorporated along with the logo.The following should be on the back of the card SPECIALIZING IN NEW AND USED TIRES & WHEELS FOR:- Loaders- Skid Steers- Telehandlers- Boom Lifts- Forklifs and moreELIMINATING DOWNTIMEWheel Exchange Program for New & Used Foam Filled and Solid Rubber TiresSPECIALTY SERVICES- Foam Filling Tires- Largest Tire Press in SE- ONSITE Forklift Tire Press- Boom Truck Services - Rubber Tracks

Target Market(s)

New and Existing Customers

Industry/Entity Type

Business

Contact Information for Business Card

NAMEHEAVY DUTY TIRE, LLC8470 Belvedere RoadWest Palm Beach, FL 33411P: 844-HD-TIRESF: 561-431-6469C:E: W: WWW.GRANITERIMSUPPLY-EXAMPLE.COM

Font styles to use
Sans Serif

Colors
f37122
333333

Requirements
Must have
• The logo and the information indicated for the backside of the card
Nice to have
• Keep the orange and charcoal grey colors

```html
<!DOCTYPE html>
<html lang="en">
<head>
<meta charset="utf-8">
<title>Granite Rim Supply, LLC – Business Card</title>
<link href="https://fonts.googleapis.com/css2?family=Open+Sans:wght@400;600;700&family=Roboto+Slab:wght@800&display=swap" rel="stylesheet">
<style>
  :root {
    --bg: #e9e6e2;
    --orange-light: #fdd39e;
    --orange-mid: #f7b06a;
    --orange-deep: #e98e45;
    --brand-orange: #f37122;
    --charcoal: #333333;
    --slate: #3e5156;
    --muted: #6b6b6b;
    --card-white: #ffffff;
    --card-grey: #e6e6e6;
    --rule-light: rgba(255,255,255,0.85);
    --rule-dark: #555555;
  }
  html, body {
    margin: 0;
    width: 1200px;
    height: 892px;
    overflow: hidden;
    background: var(--bg);
    font-family: "Open Sans", Arial, sans-serif;
  }
  .stage {
    width: 1200px;
    height: 892px;
    display: flex;
    align-items: center;
    justify-content: center;
    gap: 40px;
  }
  .card {
    position: relative;
    width: 540px;
    height: 309px;
    border-radius: 18px;
    box-shadow: 0 10px 24px rgba(0,0,0,0.18);
    overflow: hidden;
    box-sizing: border-box;
    color: var(--charcoal);
  }

  /* Front */
  .card-front {
    background: radial-gradient(ellipse at 55% 45%, var(--orange-light) 0%, var(--orange-mid) 55%, var(--orange-deep) 100%);
  }
  .company-title {
    position: absolute;
    left: 28px;
    top: 22px;
    margin: 0;
    font-family: "Roboto Slab", Georgia, serif;
    font-weight: 800;
    font-size: 26px;
    letter-spacing: 0.5px;
    color: var(--slate);
    white-space: nowrap;
  }
  .brand-mark {
    position: absolute;
    left: 34px;
    top: 168px;
    display: flex;
    align-items: center;
    gap: 12px;
  }
  .brand-mark .dot {
    width: 30px;
    height: 30px;
    border-radius: 50%;
    background: var(--charcoal);
  }
  .brand-mark .name {
    font-weight: 700;
    font-size: 22px;
    color: var(--charcoal);
    white-space: nowrap;
  }
  .details {
    position: absolute;
    left: 262px;
    top: 84px;
    font-size: 13px;
    line-height: 20px;
    white-space: nowrap;
  }
  .address { margin: 0 0 12px; }
  .divider {
    width: 240px;
    height: 1px;
    background: var(--rule-light);
    margin-bottom: 12px;
  }
  .contact-list { list-style: none; margin: 0; padding: 0; }
  .contact-list li { display: flex; align-items: center; gap: 8px; }
  .contact-list svg { flex: none; }

  /* Back */
  .card-back {
    background: linear-gradient(160deg, var(--card-white) 30%, var(--card-grey) 100%);
  }
  .back-column {
    position: absolute;
    top: 22px;
  }
  .column-left { left: 26px; width: 232px; }
  .column-right { left: 282px; width: 232px; }
  .block-title {
    margin: 0;
    font-size: 17px;
    font-weight: 400;
    letter-spacing: 1px;
    color: var(--muted);
    white-space: nowrap;
  }
  .block-title .accent { color: var(--brand-orange); }
  .block-sub {
    margin: 2px 0 0;
    font-size: 11px;
    font-weight: 600;
    color: var(--charcoal);
  }
  .block-rule {
    height: 1px;
    background: var(--rule-dark);
    margin: 6px 0 7px;
  }
  .item-list {
    list-style: none;
    margin: 0;
    padding: 0;
    font-size: 12.5px;
    line-height: 18px;
    white-space: nowrap;
  }
  .item-list li::before { content: "- "; }
  .downtime { margin-top: 14px; }
  .downtime-text {
    margin: 0;
    font-size: 12px;
    line-height: 17px;
  }
  .back-mark {
    position: absolute;
    left: 282px;
    bottom: 24px;
    display: flex;
    align-items: center;
    gap: 10px;
  }
  .back-mark .dot {
    width: 26px;
    height: 26px;
    border-radius: 50%;
    background: var(--brand-orange);
  }
  .back-mark .name {
    font-weight: 700;
    font-size: 19px;
    color: var(--charcoal);
    white-space: nowrap;
  }
</style>
</head>
<body>
<main class="stage">
  <section class="card card-front" aria-label="Business card front">
    <h1 class="company-title">GRANITE RIM SUPPLY, LLC</h1>
    <div class="brand-mark">
      <span class="dot"></span>
      <span class="name">GRANITE RIM</span>
    </div>
    <div class="details">
      <p class="address">5126 Marston Lane<br>West Palm Beach, FL 33411</p>
      <div class="divider"></div>
      <ul class="contact-list">
        <li><svg width="10" height="10" viewBox="0 0 10 10"><rect width="10" height="10" rx="1.5" fill="#333"/><rect x="3" y="2" width="4" height="6" rx="0.8" fill="#f7b06a"/></svg>0418 602 319</li>
        <li><svg width="10" height="10" viewBox="0 0 10 10"><rect width="10" height="10" rx="1.5" fill="#333"/><path d="M3 2.5 L4.5 2.5 L5 4 L4 4.8 Q5 6.5 6 6.2 L7 5.5 L7.5 7.2 Q6 8.5 3.5 6 Q2 4 3 2.5Z" fill="#f7b06a"/></svg>844-GR-WHEEL</li>
        <li><svg width="10" height="10" viewBox="0 0 10 10"><rect width="10" height="10" rx="1.5" fill="#333"/><rect x="2.5" y="3" width="5" height="4" fill="#f7b06a"/></svg>561-278-9053</li>
        <li><svg width="10" height="10" viewBox="0 0 10 10"><rect width="10" height="10" rx="1.5" fill="#333"/><path d="M2 3 H8 V7 H2Z M2 3 L5 5.5 L8 3" fill="none" stroke="#f7b06a" stroke-width="0.9"/></svg>info@graniterimsupply-example.com</li>
        <li><svg width="10" height="10" viewBox="0 0 10 10"><rect width="10" height="10" rx="1.5" fill="#333"/><circle cx="5" cy="5" r="2.6" fill="none" stroke="#f7b06a" stroke-width="0.9"/><path d="M2.4 5 H7.6" stroke="#f7b06a" stroke-width="0.8"/></svg>www.graniterimsupply-example.com</li>
      </ul>
    </div>
  </section>

  <section class="card card-back" aria-label="Business card back">
    <div class="back-column column-left">
      <h2 class="block-title"><span class="accent">SPECIALIZING</span> IN</h2>
      <p class="block-sub">NEW AND USED TIRES &amp; WHEELS FOR:</p>
      <div class="block-rule"></div>
      <ul class="item-list">
        <li>Loaders</li>
        <li>Skid Steers</li>
        <li>Telehandlers</li>
        <li>Boom Lifts</li>
        <li>Forklifts and more</li>
      </ul>
      <div class="downtime">
        <h2 class="block-title"><span class="accent">ELIMINATING</span> DOWNTIME</h2>
        <div class="block-rule"></div>
        <p class="downtime-text">Wheel Exchange Program for New &amp; Used<br>Foam Filled and Solid Rubber Tires</p>
      </div>
    </div>
    <div class="back-column column-right">
      <h2 class="block-title"><span class="accent">SPECIALTY</span> SERVICES</h2>
      <div class="block-rule"></div>
      <ul class="item-list">
        <li>Foam Filling Tires</li>
        <li>Largest Tire Press in SE</li>
        <li>ONSITE Forklift Tire Press</li>
        <li>Boom Truck Services</li>
        <li>Rubber Tracks</li>
      </ul>
    </div>
    <div class="back-mark">
      <span class="dot"></span>
      <span class="name">GRANITE RIM</span>
    </div>
  </section>
</main>
</body>
</html>
```